Super Global Luxury Business Cards!!!

I need a luxury business card design for a realtor that specializes in luxury homes

Industry/Entity Type

Real Estate

Contact Information for Business Card

a nice luxury design that will make people go WOW this is a NICE card

Requirements
Must have
• my name, phone, email, social media - address - use of both logos

```html
<!DOCTYPE html>
<html lang="en">
<head>
<meta charset="utf-8">
<title>Vale Estates – Business Card</title>
<link href="https://fonts.googleapis.com/css2?family=Montserrat:wght@400;500;700&display=swap" rel="stylesheet">
<style>
  :root {
    --backdrop: #3b332e;
    --card: #262626;
    --card-back: #151515;
    --pattern-light: #2a2a2a;
    --pattern-dark: #0f0f0f;
    --ink: #ffffff;
    --ink-soft: #d8d8d8;
    --rule: #bdbdbd;
  }
  * { box-sizing: border-box; margin: 0; padding: 0; }
  html, body {
    width: 1200px; height: 786px; overflow: hidden;
    background: var(--backdrop);
    font-family: "Montserrat", sans-serif;
  }
  .canvas {
    position: relative; width: 1200px; height: 786px;
    display: flex; align-items: center; justify-content: center; gap: 40px;
  }
  .card {
    width: 540px; height: 309px; border-radius: 4px;
    box-shadow: 0 14px 30px rgba(0,0,0,.45);
    position: relative; overflow: hidden;
  }
  .card--front { background: var(--card); display: flex; align-items: center; }
  .brand {
    width: 245px; display: flex; align-items: center; justify-content: center; gap: 12px;
  }
  .brand__circle {
    width: 26px; height: 26px; border: 2px solid var(--ink); border-radius: 50%; flex: none;
  }
  .brand__name {
    color: var(--ink); font-weight: 500; font-size: 24px; letter-spacing: 3px; text-transform: uppercase;
    line-height: 1.15;
  }
  .divider { width: 1px; height: 196px; background: var(--rule); }
  .details { padding-left: 30px; color: var(--ink-soft); }
  .details__name { color: var(--ink); font-weight: 700; font-size: 18px; }
  .details__title { font-size: 11px; margin-top: 2px; margin-bottom: 14px; }
  .contact { list-style: none; font-size: 11.5px; line-height: 19px; }
  .contact li { display: flex; align-items: center; gap: 10px; }
  .contact svg { width: 11px; height: 11px; fill: var(--ink-soft); flex: none; }
  .address { font-size: 11.5px; line-height: 17px; margin-top: 12px; }
  .card--back { background: var(--card-back); }
  .back__pattern {
    position: absolute; inset: 0;
    background: linear-gradient(100deg, var(--pattern-light) 0%, var(--pattern-dark) 55%, var(--pattern-light) 100%);
  }
  .back__mark {
    position: absolute; right: 34px; top: 120px;
    display: flex; align-items: center; gap: 8px;
  }
  .back__mark .brand__circle { width: 14px; height: 14px; border-width: 1.5px; }
  .back__mark .brand__name { font-size: 11px; letter-spacing: 2px; }
</style>
</head>
<body>
<main class="canvas">
  <section class="card card--front">
    <div class="brand">
      <span class="brand__circle"></span>
      <span class="brand__name">Vale<br>Estates</span>
    </div>
    <div class="divider"></div>
    <div class="details">
      <h1 class="details__name">Daniel Hart</h1>
      <p class="details__title">Managing Director</p>
      <ul class="contact">
        <li><svg viewBox="0 0 24 24"><path d="M6.6 10.8a15 15 0 0 0 6.6 6.6l2.2-2.2a1 1 0 0 1 1-.25 11.4 11.4 0 0 0 3.6.57 1 1 0 0 1 1 1V20a1 1 0 0 1-1 1A17 17 0 0 1 3 4a1 1 0 0 1 1-1h3.5a1 1 0 0 1 1 1c0 1.25.2 2.45.57 3.57a1 1 0 0 1-.25 1z"/></svg>555.201.4830</li>
        <li><svg viewBox="0 0 24 24"><path d="M2 5h20v14H2zm2 2v.5l8 5 8-5V7z"/></svg>info@valeestates.com</li>
        <li><svg viewBox="0 0 24 24"><path d="M12 2a10 10 0 1 0 0 20 10 10 0 0 0 0-20zm0 2c1.2 1.5 2 3.6 2.2 6H9.8C10 7.6 10.8 5.5 12 4zm-2.2 8h4.4c-.2 2.4-1 4.5-2.2 6-1.2-1.5-2-3.6-2.2-6z"/></svg>www.valeestates.com</li>
      </ul>
      <p class="address">1470 Harbor View Blvd<br>Palm Shore, Florida 30000</p>
    </div>
  </section>
  <section class="card card--back">
    <div class="back__pattern" role="img" aria-label="Tone-on-tone repeating brand pattern in glossy black"></div>
    <div class="back__mark">
      <span class="brand__circle"></span>
      <span class="brand__name">Vale Estates</span>
    </div>
  </section>
</main>
</body>
</html>
```